Current website re-design to a updated look and feel.

We currently have a website www.brightlanefreight.com that we want to give an updated look and feel to. We are a logistics company that competes with Pellwick, Dm Harrowgate, Quill but on a smaller scale. We want something fresh and updated. We have two locations one in downtown Chicago, IL and one in Palatine IL. We are a fun group that also gets the job done. We know we need pictures of both locations and possibly a video, but we need fresh design ideas. The 'who we are' page is really the only page that we currently want to keep. The 'what we do' page needs to be completely re-done from a look and feel for sure.

Target Market(s)

Anyone who uses Truck transportation to move their product. Mainly US manufacturers.

Industry/Entity Type

Logistics

Number of Pages Required

5+ page

Font styles to use
Sans Serif

Colors
5c91c4
0355a3
d0dfed

Requirements
Must have
• The new design must entice people to want to do business with us. The design must have locations for pictures and at least one video which we know we will have to provide. Design must be easy to navigate.

```html
<!DOCTYPE html>
<html lang="en">
<head>
<meta charset="utf-8">
<title>Brightlane Freight</title>
<link href="https://fonts.googleapis.com/css2?family=Open+Sans:wght@400;600;700&display=swap" rel="stylesheet">
<style>
:root{
  --brand-light:#5c91c4;
  --brand-deep:#0355a3;
  --brand-pale:#d0dfed;
  --band-pale:#edf5fc;
  --grey-band:#f3f3f3;
  --text:#333;
  --text-soft:#666;
  --footer:#444;
  --white:#fff;
}
*{box-sizing:border-box;margin:0;padding:0}
html,body{width:1200px;height:2261px;overflow:hidden}
body{font-family:"Open Sans",Arial,sans-serif;color:var(--text);background:var(--white);position:relative}
.abs{position:absolute}

.site-header{position:absolute;left:0;top:0;width:1200px;height:107px;background:var(--white)}
.brand{left:133px;top:26px;display:flex;align-items:center;gap:10px;color:var(--brand-deep);font-size:30px;font-weight:400;letter-spacing:-.5px}
.brand-dot{width:14px;height:14px;border-radius:50%;background:var(--brand-deep)}
.login{right:133px;top:20px;font-size:13px;color:var(--brand-deep);display:flex;align-items:center;gap:6px}
.main-nav{right:133px;top:66px;display:flex;gap:32px;font-size:12.5px;color:#555}
.main-nav .active{color:var(--brand-deep)}

.hero{left:0;top:107px;width:1200px;height:507px;background:linear-gradient(180deg,#41586f 0%,#6d7d8c 30%,#4f5d68 55%,#3d4e5c 100%)}
.hero-media{position:absolute;inset:0;background:linear-gradient(90deg,rgba(160,60,40,.35) 0%,rgba(40,90,120,.25) 25%,rgba(60,60,60,.3) 50%,rgba(40,90,120,.25) 75%,rgba(160,60,40,.35) 100%)}
.hero-title{position:absolute;left:0;width:1200px;top:248px;text-align:center;color:var(--white);font-size:32px;font-weight:700;line-height:40px;text-transform:uppercase;letter-spacing:.3px}
.play{position:absolute;left:574px;top:186px}
.hero-arrow{position:absolute;top:240px}

.service{width:300px;text-align:center}
.service h2{color:var(--brand-light);font-size:23px;font-weight:700;line-height:25px;text-transform:uppercase}
.service p{font-size:10.5px;line-height:15px;color:var(--text);margin-top:8px;padding:0 6px}
.read-more{display:inline-block;margin-top:14px;width:82px;height:37px;line-height:35px;border:1px solid #ccc;font-size:10.5px;color:#555}

.founder-band{left:0;top:1007px;width:1200px;height:279px;background:var(--band-pale)}
.founder-photo{left:133px;top:1057px;width:178px;height:179px;background:linear-gradient(180deg,#f2f2f2,#d9d6cf)}
.founder-text{left:339px;top:1046px;width:730px}
.founder-text h2{color:var(--brand-deep);font-size:32px;font-weight:700;text-transform:uppercase;line-height:44px}
.founder-text p{font-size:10.5px;line-height:16px;margin-top:8px}

.pillar{width:440px}
.pillar h2{color:var(--brand-light);font-size:31px;font-weight:700;text-transform:uppercase;line-height:38px;margin-top:12px}
.pillar p{font-size:12.8px;line-height:19.5px;color:var(--text-soft);margin-top:6px;letter-spacing:-.1px}

.grey-band{left:0;top:1654px;width:1200px;height:351px;background:var(--grey-band)}
.block-title{color:var(--brand-light);font-size:24px;font-weight:700;text-transform:uppercase;line-height:30px}
.block-text{font-size:10.5px;line-height:16px;margin-top:6px}
.btn{display:inline-block;background:var(--brand-light);color:var(--white);font-size:12px;text-transform:uppercase;text-align:center}
.badge{border:1px solid #ccd;background:var(--white)}
.field{width:211px;height:34px;border:1px solid #ccc;background:var(--white);font-size:10.5px;color:#888;padding:0 14px;line-height:32px}

.contact{top:2048px;font-size:12px;line-height:24px;color:#555;display:flex;gap:8px}
.contact svg{margin-top:7px;flex:none}

.site-footer{left:0;top:2165px;width:1200px;height:96px;background:var(--footer)}
.footer-nav{left:133px;top:26px;font-size:10.5px;color:#ddd}
.copyright{left:133px;top:50px;font-size:10.5px;color:#ccc}
.social{top:36px;width:25px;height:25px;border-radius:50%}
</style>
</head>
<body>

<header class="site-header">
  <div class="abs brand"><span class="brand-dot"></span>Brightlane Freight</div>
  <div class="abs login">
    <svg width="10" height="12" viewBox="0 0 10 12"><rect x="1" y="5" width="8" height="7" fill="#0355a3"/><path d="M3 5V3a2 2 0 0 1 4 0" stroke="#0355a3" stroke-width="1.5" fill="none"/></svg>
    LOG IN
  </div>
  <nav class="abs main-nav">
    <span class="active">What We Do</span><span>How We Do It</span><span>Who We Are</span><span>Tracking</span><span>Contact</span>
  </nav>
</header>

<section class="abs hero">
  <div class="hero-media" role="img" aria-label="Video still of a container port with cranes and stacked shipping containers"></div>
  <svg class="play" width="48" height="48" viewBox="0 0 48 48"><circle cx="24" cy="24" r="24" fill="#fff"/><path d="M19 14l15 10-15 10z" fill="#222"/></svg>
  <h1 class="hero-title">Praesent imperdiet eros vitae<br>augue luctus pretium</h1>
  <svg class="hero-arrow" style="left:4px" width="16" height="26" viewBox="0 0 16 26"><path d="M12 3L4 13l8 10" stroke="#fff" stroke-width="2" fill="none"/></svg>
  <svg class="hero-arrow" style="right:4px" width="16" height="26" viewBox="0 0 16 26"><path d="M4 3l8 10-8 10" stroke="#fff" stroke-width="2" fill="none"/></svg>
</section>

<section>
  <div class="abs service" style="left:126px;top:690px">
    <svg width="80" height="48" viewBox="0 0 80 48"><rect x="18" y="6" width="20" height="22" fill="none" stroke="#0355a3" stroke-width="4"/><rect x="12" y="24" width="38" height="14" fill="#0355a3"/><rect x="50" y="4" width="4" height="36" fill="#0355a3"/><rect x="54" y="36" width="16" height="4" fill="#0355a3"/><circle cx="20" cy="42" r="5" fill="#0355a3"/><circle cx="42" cy="42" r="5" fill="#0355a3"/></svg>
    <h2 style="margin-top:8px">Freight<br>Management</h2>
    <p>We strive for a perfect delivery and promise to be there for anything you may need, every step of the way. Click here to find out more about Freight Management and how we do it.</p>
    <span class="read-more">Read more</span>
  </div>
  <div class="abs service" style="left:450px;top:690px">
    <svg width="80" height="48" viewBox="0 0 80 48"><rect x="10" y="8" width="40" height="28" fill="#0355a3"/><path d="M52 16h12l8 10v10H52z" fill="#0355a3"/><circle cx="22" cy="40" r="6" fill="#0355a3" stroke="#fff" stroke-width="2"/><circle cx="60" cy="40" r="6" fill="#0355a3" stroke="#fff" stroke-width="2"/></svg>
    <h2 style="margin-top:8px">Transportation</h2>
    <p>With a combined 500+ years of industry experience between all employees, we are the logistics company you need to get the job done right. Click here to find out more about our transportation expertise.</p>
    <span class="read-more">Read more</span>
  </div>
  <div class="abs service" style="left:774px;top:690px">
    <svg width="80" height="48" viewBox="0 0 80 48"><rect x="30" y="2" width="20" height="20" fill="#0355a3"/><rect x="18" y="26" width="20" height="20" fill="#0355a3"/><rect x="42" y="26" width="20" height="20" fill="#0355a3"/><path d="M34 8l6 10M40 8l6 10M22 32l6 10M28 32l6 10M46 32l6 10M52 32l6 10" stroke="#fff" stroke-width="1.5"/></svg>
    <h2 style="margin-top:8px">Warehouse &amp;<br>Distribution</h2>
    <p>Our secure facility can accommodate large or small quantities of product. Our inventory management system provides real-time visibility.</p>
    <span class="read-more">Read more</span>
  </div>
</section>

<section>
  <div class="abs founder-band"></div>
  <div class="abs founder-photo" role="img" aria-label="Portrait photo of the company founder"></div>
  <div class="abs founder-text">
    <h2>Welcome from our founder</h2>
    <p>Brightlane Freight welcomes you to our growing family of clients! We have over 26 years of experience in helping people solve their logistics needs from coast-to-coast. We also provide friendly, exceptional service that makes it easy to do business with us. Give us a call today and experience the difference for yourself!</p>
    <p style="margin-top:14px">"Our service commitment begins from the moment you contact us. We appreciate your trust, and we go the extra mile to ensure that your freight is handled with care and expediency. If an issue comes up, we work tirelessly to resolve it, staying in contact with you until your freight is delivered without issue!"</p>
    <p style="margin-top:14px">Let us take the worry out of your logistics. Relax, we've got this! - Marla Dennick, Founder</p>
  </div>
</section>

<section>
  <div class="abs pillar" style="left:131px;top:1362px">
    <svg width="42" height="26" viewBox="0 0 42 26"><path d="M2 13C10 2 32 2 40 13 32 24 10 24 2 13z" fill="none" stroke="#5c91c4" stroke-width="3"/><circle cx="21" cy="13" r="6" fill="#5c91c4"/></svg>
    <h2>Brightlane Vision</h2>
    <p>Brightlane vision is to be the premier third party logistics solution in North America. We will become premier by providing superior customer service, efficient and cost effective warehousing and distribution solutions. The decisions we make today for hiring, training, technology, strategic services and customer satisfaction are based on this vision.</p>
  </div>
  <div class="abs pillar" style="left:630px;top:1364px">
    <svg width="36" height="36" viewBox="0 0 36 36"><circle cx="18" cy="18" r="16" fill="none" stroke="#5c91c4" stroke-width="3"/><circle cx="18" cy="18" r="10" fill="none" stroke="#5c91c4" stroke-width="3"/><circle cx="18" cy="18" r="4" fill="#5c91c4"/></svg>
    <h2 style="margin-top:10px">Brightlane Mission</h2>
    <p>Brightlane's mission is to provide the most thorough and satisfying third-party logistics experience for its customers. Brightlane uses leading technologies and an industry experienced staff to deliver an unparalleled customer service experience. Brightlane leverages the most efficient mode of transportation, and tailors cost effective solutions for warehousing and distribution of your products in every situation.</p>
  </div>
</section>

<section>
  <div class="abs grey-band"></div>
  <div class="abs" style="left:131px;top:1726px;width:440px">
    <h3 class="block-title">Carriers</h3>
    <p class="block-text">Are you a carrier looking to work with Brightlane? Click here to find out why we have the best carrier relationships in the business.</p>
  </div>
  <span class="abs btn" style="left:131px;top:1809px;width:139px;height:35px;line-height:35px">Apply now</span>
  <div class="abs badge" style="left:131px;top:1863px;width:163px;height:61px" role="img" aria-label="Business ethics award badge"></div>
  <div class="abs badge" style="left:310px;top:1865px;width:129px;height:57px;border-radius:14px;border-color:#1a7a6e" role="img" aria-label="Certification badge"></div>

  <div class="abs" style="left:630px;top:1726px;width:440px">
    <h3 class="block-title">Get updates</h3>
    <p class="block-text">We occasionally send out news and related industry articles. Sign up and we promise to deliver quality information to you.</p>
  </div>
  <div class="abs field" style="left:632px;top:1807px">First Name</div>
  <div class="abs field" style="left:855px;top:1807px">Last Name</div>
  <div class="abs field" style="left:632px;top:1853px">Organization</div>
  <div class="abs field" style="left:855px;top:1853px">Email</div>
  <span class="abs btn" style="left:632px;top:1899px;width:71px;height:35px;line-height:35px">Submit</span>
</section>

<section>
  <div class="abs contact" style="left:133px">
    <svg width="9" height="12" viewBox="0 0 9 12"><path d="M4.5 0A4.5 4.5 0 0 1 9 4.5C9 8 4.5 12 4.5 12S0 8 0 4.5A4.5 4.5 0 0 1 4.5 0z" fill="#666"/><circle cx="4.5" cy="4.5" r="1.6" fill="#fff"/></svg>
    <div style="line-height:19px;margin-top:3px">418 W Orchard Ave&nbsp; Suite 210<br>Marlow Heights, IL&nbsp;&nbsp; 60199</div>
  </div>
  <div class="abs contact" style="left:339px">
    <svg width="11" height="11" viewBox="0 0 11 11"><path d="M2 0l2 3-1.2 1.2a7 7 0 0 0 4 4L8 7l3 2-1.5 2C5 11 0 6 0 1.5z" fill="#666"/></svg>
    <div>Office Phone: 847.555.0140<br>Warehouse: 847.555.0142</div>
  </div>
  <div class="abs contact" style="left:567px">
    <svg width="11" height="11" viewBox="0 0 11 11"><rect x="2" y="0" width="7" height="4" fill="#666"/><rect x="0" y="4" width="11" height="7" fill="#666"/></svg>
    <div>Fax: 847.555.0141</div>
  </div>
  <div class="abs contact" style="left:749px">
    <svg width="11" height="9" viewBox="0 0 11 9"><rect width="11" height="9" fill="#666"/><path d="M0 0l5.5 5L11 0" stroke="#fff" fill="none"/></svg>
    <div>Rates: rates@brightlanefreight.com<br>Warehouse: warehouse@brightlanefreight.com<br>Information: info@brightlanefreight.com</div>
  </div>
</section>

<footer class="abs site-footer">
  <div class="abs footer-nav">What We Do &nbsp;&nbsp;|&nbsp;&nbsp; How We Do It &nbsp;&nbsp;|&nbsp;&nbsp; Who We Are &nbsp;&nbsp;|&nbsp;&nbsp; Tracking &nbsp;&nbsp;|&nbsp;&nbsp; Contact</div>
  <div class="abs copyright">Copyright &copy; 2017 Brightlane Freight. All rights reserved.</div>
  <span class="abs social" style="left:1008px;background:#3b5998"></span>
  <span class="abs social" style="left:1041px;background:#1da1f2"></span>
</footer>

</body>
</html>
```